Core values in our company OKV (Residency and Relocation)

Do good:
1. Being Direct and communicative for the benefit of all parties
2. Working for the Benefit of the company, client and team members
3. Wanting to improve to create a better impact
4. Having healthy rivalry
Be ahead of curve:
1. Having the confidence to break through barriers which arise
2. Desire to grow and learn towards establishment and agreed goal
3. Getting off the sidelines and get into the game
4. Keeping the end game in mind having due regard to processes and milestones
5. Self starter and works on own initiative
6. Diligent and impactful in your field of responsibility
Truth and Honesty
2. Have the confidence and ability to speak what you really want to communicate
3. Being truthful to yourself, clients and colleagues to find the innovations that lie within
4. Seeking the truth by opening things up for discussion
5. Being Optimistic
Background Information on our Company:OKV is a professional law firm in London Docklands. We caters for both private and corporate clients ranging from highly regarded and established law firms to boutique and niche immigration practices. We also specialises in expert legal advice and prides itself on providing services that go beyond the expectations of its clients.
What we need: We need a Poster about Truth and Honesty, this is to show one of our values as a company. It will need to be vibrant and straight to the point. Colours can be orange grey white and yellow. Attached is our company logo.
Reason: To remind colleagues that this is one of our main values and it is instilled in our company.
Things we would like:
1. To create a point of focus
2. Use shapes to create visual interest
3. Use creative illustrations
4. Take the viewer’s focus on a journey with clever perspective
Industry/Entity Type
Legal
Requirements
Must have
- a globe (Picture)
- Do good:
- 1. Being Direct and communicative for the benefit of all parties
- 2. Working for the Benefit of the company, client and team members
- 3. Wanting to improve to create a better impact
- 4. Having healthy rivalry
- Be ahead of curve:
- 1. Having the confidence to break through barriers which arise
- 2. Desire to grow and learn towards establishment and agreed goal
- 3. Getting off the sidelines and get into the game
- 4. Keeping the end game in mind having due regard to processes and milestones
- 5. Self starter and works on own initiative
- 6. Diligent and impactful in your field of responsibility
- Truth and Honesty
- 2. Have the confidence and ability to speak what you really want to communicate
- 3. Being truthful to yourself, clients and colleagues to find the innovations that lie within
- 4. Seeking the truth by opening things up for discussion
- 5. Being Optimistic

```html
<!DOCTYPE html>
<html lang="en">
<head>
<meta charset="utf-8">
<title>OKV Core Values Poster Options</title>
<link rel="stylesheet" href="https://fonts.googleapis.com/css2?family=Roboto+Condensed:wght@400;700&family=Archivo+Black&display=swap">
<style>
  :root {
    --board: #3a3a37;
    --cream-light: #fdf4d6;
    --cream-deep: #f7dc93;
    --orange: #f08a1c;
    --yellow: #f7b51e;
    --charcoal: #3b3b3b;
    --ink: #2a2a2a;
    --space-dark: #1d140e;
    --space-warm: #8a4a12;
    --space-glow: #e0892a;
    --white: #ffffff;
  }
  * { box-sizing: border-box; margin: 0; padding: 0; }
  html, body { width: 1200px; height: 650px; overflow: hidden; }
  body {
    background: var(--board);
    font-family: "Roboto Condensed", "Arial Narrow", sans-serif;
    color: var(--ink);
    position: relative;
  }

  .poster {
    position: absolute;
    top: 73px;
    width: 338px;
    height: 477px;
    background: linear-gradient(160deg, var(--cream-light) 0%, #fbeab4 55%, var(--cream-deep) 100%);
    box-shadow: 0 6px 18px rgba(0,0,0,0.55);
    overflow: hidden;
  }
  .poster--one { left: 69px; }
  .poster--two { left: 424px; }
  .poster--three { left: 779px; }

  .option-label {
    position: absolute;
    top: 582px;
    width: 338px;
    text-align: center;
    font-family: "Archivo Black", "Arial Black", sans-serif;
    font-size: 30px;
    letter-spacing: 1px;
    color: var(--white);
  }
  .option-label--one { left: 69px; }
  .option-label--two { left: 424px; }
  .option-label--three { left: 779px; }

  /* brand block */
  .brand {
    position: absolute;
    text-align: center;
    width: 180px;
  }
  .brand-name {
    display: block;
    font-weight: 700;
    font-size: 40px;
    line-height: 40px;
    color: var(--orange);
    letter-spacing: 1px;
  }
  .brand-tagline {
    display: block;
    font-size: 9px;
    color: var(--charcoal);
    margin-top: 2px;
  }

  /* space imagery areas */
  .visual {
    position: absolute;
    background: radial-gradient(ellipse at 55% 40%, var(--space-glow) 0%, var(--space-warm) 35%, var(--space-dark) 80%);
  }
  .visual--strip { left: 200px; top: 0; width: 138px; height: 477px;
    background:
      radial-gradient(circle at 65% 88%, #f4a347 0%, #8c4511 22%, transparent 40%),
      radial-gradient(ellipse at 45% 52%, #d98a3a 0%, #6d3a12 25%, transparent 48%),
      radial-gradient(ellipse at 60% 14%, #b77a43 0%, #4a2c16 28%, transparent 50%),
      linear-gradient(180deg, #2a1c12 0%, #3d230f 50%, #24140a 100%);
  }
  .visual--satellite { left: 183px; top: 0; width: 155px; height: 196px;
    background: radial-gradient(ellipse at 45% 35%, #a06a3a 0%, #4a2e18 45%, #1e140d 90%); }
  .visual--astronaut { left: 0; top: 180px; width: 165px; height: 152px;
    background: radial-gradient(ellipse at 35% 50%, #f3c23a 0%, #a7701a 35%, #2a1d0e 85%); }
  .visual--earth { left: 183px; top: 353px; width: 155px; height: 124px;
    background: radial-gradient(circle at 40% 60%, #d9d9d9 0%, #6a6a6a 30%, #1a1a1a 75%); }

  /* stacked layout copy */
  .copy { position: absolute; left: 0; top: 0; width: 200px; height: 477px; }

  .tag {
    position: absolute;
    left: 27px;
    height: 19px;
    padding: 0 6px;
    border-radius: 5px;
    font-size: 14px;
    line-height: 19px;
    color: var(--white);
    white-space: nowrap;
  }
  .tag::after {
    content: "";
    position: absolute;
    left: 10px;
    bottom: -5px;
    border-left: 4px solid transparent;
    border-right: 4px solid transparent;
    border-top: 5px solid currentColor;
  }
  .tag--good { top: 95px; background: var(--orange); font-weight: 400; }
  .tag--good::after { border-top-color: var(--orange); }
  .tag--curve { top: 200px; background: var(--yellow); }
  .tag--curve::after { border-top-color: var(--yellow); }
  .tag--truth { top: 339px; background: var(--charcoal); }
  .tag--truth::after { border-top-color: var(--charcoal); }

  .values {
    position: absolute;
    list-style: none;
    font-size: 7px;
    line-height: 9.4px;
    font-weight: 700;
    color: var(--ink);
  }
  .values li { position: relative; padding-left: 9px; margin-bottom: 3.6px; }
  .values li::before {
    content: "";
    position: absolute;
    left: 0;
    top: 2px;
    width: 5px;
    height: 5px;
    background: var(--marker);
  }
  .values--linked::before {
    content: "";
    position: absolute;
    left: 2px;
    top: 4px;
    bottom: 8px;
    width: 1px;
    background: var(--marker);
  }
  .values--good { --marker: var(--orange); }
  .values--curve { --marker: var(--yellow); }
  .values--truth { --marker: var(--charcoal); }

  .copy .values { left: 22px; width: 170px; }
  .copy .values--good { top: 124px; }
  .copy .values--curve { top: 229px; }
  .copy .values--truth { top: 369px; }

  /* grid layout (option three) */
  .panel { position: absolute; background: linear-gradient(160deg, var(--cream-light), #fae6a8); }
  .panel--curve { left: 165px; top: 195px; width: 173px; height: 158px; }

  .heading {
    position: absolute;
    font-size: 15px;
    line-height: 17px;
    padding-bottom: 2px;
    border-bottom: 2px solid currentColor;
  }
  .heading--good { left: 18px; top: 83px; width: 162px; color: var(--orange); }
  .heading--curve { left: 9px; top: 9px; width: 164px; color: var(--yellow); }
  .heading--truth { left: 18px; top: 336px; width: 158px; color: var(--charcoal); }

  .poster--three .values { font-weight: 400; font-size: 7px; }
  .poster--three .values--good { left: 18px; top: 108px; width: 160px; }
  .panel--curve .values--curve { left: 9px; top: 33px; width: 160px; }
  .poster--three .values--truth { left: 18px; top: 362px; width: 160px; }
</style>
</head>
<body>

  <!-- Option 01 -->
  <article class="poster poster--one">
    <div class="copy">
      <div class="brand" style="left:25px; top:22px;">
        <span class="brand-name">OKV</span>
        <span class="brand-tagline">residency and relocation</span>
      </div>
      <h2 class="tag tag--good">DO GOOD:</h2>
      <ul class="values values--good values--linked">
        <li>Being Direct and communicative for the benefit of all parties</li>
        <li>Working for the Benefit of the company, client and team members</li>
        <li>Wanting to improve to create a better impact</li>
        <li>Having healthy rivalry</li>
      </ul>
      <h2 class="tag tag--curve">Be a Head of Curve:</h2>
      <ul class="values values--curve values--linked">
        <li>Having the confidence to break through barriers which arise</li>
        <li>Desire to grow and learn towards establishment and agreed goal</li>
        <li>Getting off the sidelines and get into the game</li>
        <li>Keeping the end game in mind having due regard to processes and milestones</li>
        <li>Self starter and works on own initiative</li>
        <li>Diligent and impactful in your field of responsibility</li>
      </ul>
      <h2 class="tag tag--truth">Truth and Honesty</h2>
      <ul class="values values--truth values--linked">
        <li>Having the confidence to break through barriers which arise</li>
        <li>Have the confidence and ability to speak what you really want to communicate</li>
        <li>Being truthful to yourself, clients and colleagues to find the innovations that lie within</li>
        <li>Seeking the truth by opening things up for discussion</li>
        <li>Being Optimistic</li>
      </ul>
    </div>
    <div class="visual visual--strip" role="img" aria-label="Space scene with a satellite, a floating astronaut and a glowing globe with its moon"></div>
  </article>

  <!-- Option 02 -->
  <article class="poster poster--two">
    <div class="copy">
      <div class="brand" style="left:25px; top:22px;">
        <span class="brand-name">OKV</span>
        <span class="brand-tagline">residency and relocation</span>
      </div>
      <h2 class="tag tag--good">DO GOOD:</h2>
      <ul class="values values--good values--linked">
        <li>Being Direct and communicative for the benefit of all parties</li>
        <li>Working for the Benefit of the company, client and team members</li>
        <li>Wanting to improve to create a better impact</li>
        <li>Having healthy rivalry</li>
      </ul>
      <h2 class="tag tag--curve">Be a Head of Curve:</h2>
      <ul class="values values--curve values--linked">
        <li>Having the confidence to break through barriers which arise</li>
        <li>Desire to grow and learn towards establishment and agreed goal</li>
        <li>Getting off the sidelines and get into the game</li>
        <li>Keeping the end game in mind having due regard to processes and milestones</li>
        <li>Self starter and works on own initiative</li>
        <li>Diligent and impactful in your field of responsibility</li>
      </ul>
      <h2 class="tag tag--truth">Truth and Honesty</h2>
      <ul class="values values--truth values--linked">
        <li>Having the confidence to break through barriers which arise</li>
        <li>Have the confidence and ability to speak what you really want to communicate</li>
        <li>Being truthful to yourself, clients and colleagues to find the innovations that lie within</li>
        <li>Seeking the truth by opening things up for discussion</li>
        <li>Being Optimistic</li>
      </ul>
    </div>
    <div class="visual visual--strip" role="img" aria-label="Space scene with a satellite, a floating astronaut and a glowing globe with its moon"></div>
  </article>

  <!-- Option 03 -->
  <article class="poster poster--three">
    <div class="visual visual--satellite" role="img" aria-label="Satellite orbiting in warm-toned space"></div>
    <div class="visual visual--astronaut" role="img" aria-label="Astronaut floating in golden space light"></div>
    <div class="visual visual--earth" role="img" aria-label="Monochrome globe with its moon"></div>

    <div class="brand" style="left:5px; top:10px;">
      <span class="brand-name">OKV</span>
      <span class="brand-tagline">residency and relocation</span>
    </div>

    <h2 class="heading heading--good">DO GOOD</h2>
    <ul class="values values--good">
      <li>Being Direct and communicative for the benefit of all parties</li>
      <li>Working for the Benefit of the company, client and team members</li>
      <li>Wanting to improve to create a better impact</li>
      <li>Having healthy rivalry</li>
    </ul>

    <section class="panel panel--curve">
      <h2 class="heading heading--curve">Be a Head of Curve</h2>
      <ul class="values values--curve">
        <li>Having the confidence to break through barriers which arise</li>
        <li>Desire to grow and learn towards establishment and agreed goal</li>
        <li>Getting off the sidelines and get into the game</li>
        <li>Keeping the end game in mind having due regard to processes and milestones</li>
        <li>Self starter and works on own initiative</li>
        <li>Diligent and impactful in your field of responsibility</li>
      </ul>
    </section>

    <h2 class="heading heading--truth">Truth and Honesty</h2>
    <ul class="values values--truth">
      <li>Having the confidence to break through barriers which arise</li>
      <li>Have the confidence and ability to speak what you really want to communicate</li>
      <li>Being truthful to yourself, clients and colleagues to find the innovations that lie within</li>
      <li>Seeking the truth by opening things up for discussion</li>
      <li>Being Optimistic</li>
    </ul>
  </article>

  <p class="option-label option-label--one">OPTION 01</p>
  <p class="option-label option-label--two">OPTION 02</p>
  <p class="option-label option-label--three">OPTION 03</p>

</body>
</html>
```